Brightline Energy Product Distribution Brochure

We are looking to have our current brochure for our customers completely redesigned...the idea is to present the relevant information in an attractive way . Our website is brightlineenergyco.example where you can find more information about us. We have included a file with a rough idea of the page order and what each should include but feel free to adapt based on design. The example provided is only for context and doesnt have to be maintained. We will be using the brochure both digitally and in print form. As long as it reads easily and is eye catching, the design can be horizontal or vertical.Final deliverable should be indesign file.

"Our Brands" page: should be limited to one page (space being enough) where it has the header for each one (for example diesel generators) space for one or two lines of text and then the corresponding logos for each of the five categories
Updates

For those asking: the "our brands" page should be a single page layout where there is a header with the corresponding section and space for maybe one line of text followed by the two logos for that category. Each of the product pages should be similar in fashion to the one in the document attached: a photo of the product with some white space and space for the text to be included. We will be posting additional examples today

Target Market(s)

We want to present it to customers both digitally and in print so they can see our products

Industry/Entity Type

Power Generation

Font styles to use
Serif

Requirements
Must have
• Eye catching and able to present the information in a presentable fashion. Rest is up to you.
Nice to have
• Should incorporate the colors of our logo but can also add other depending on design

```html
<!DOCTYPE html>
<html lang="en">
<head>
<meta charset="utf-8">
<title>Brightline Energy – Distributor Program Guide</title>
<link rel="stylesheet" href="https://fonts.googleapis.com/css2?family=Raleway:wght@300;400;600;700&family=Montserrat:wght@400;600;700&display=swap">
<style>
  :root {
    --ink: #3a3838;
    --ink-deep: #2f2d2d;
    --gold: #fcc800;
    --paper: #ffffff;
    --canvas: #f2f2f2;
    --mist: #e3e3e3;
    --muted: #bdbcbc;
    --photo-dark: #4a4a4a;
    --photo-light: #cfcfcf;
  }
  * { box-sizing: border-box; margin: 0; padding: 0; }
  html, body { width: 1200px; height: 1200px; overflow: hidden; background: var(--canvas); }
  body { position: relative; font-family: "Raleway", sans-serif; }

  .page {
    position: absolute; width: 375px; height: 533px;
    background: var(--ink); overflow: hidden;
    box-shadow: 0 12px 28px rgba(0,0,0,.18);
  }
  .col-1 { left: 25px; } .col-2 { left: 412px; } .col-3 { left: 800px; }
  .row-1 { top: 40px; } .row-2 { top: 620px; }

  .page-art { position: absolute; inset: 0; width: 100%; height: 100%; }

  .photo {
    position: absolute; border-radius: 6px;
    background: linear-gradient(135deg, var(--photo-light), var(--photo-dark));
  }

  .section-tag { position: absolute; top: 24px; left: 0; display: flex; align-items: center; gap: 8px; }
  .section-tag::before { content: ""; width: 33px; height: 5px; background: var(--gold); }
  .section-tag span { font-family: "Montserrat", sans-serif; font-size: 7px; color: var(--muted); letter-spacing: .3px; }

  .brand {
    position: absolute; top: 20px; right: 30px; display: flex; align-items: center; gap: 5px;
    font-family: "Raleway", sans-serif; font-weight: 400; font-size: 8.5px; color: var(--gold); letter-spacing: .3px;
  }
  .brand::before { content: ""; width: 12px; height: 12px; border: 2px solid var(--gold); }

  .page-title {
    position: absolute; left: 33px; top: 62px;
    font-weight: 300; font-size: 21px; line-height: 1.15; color: var(--paper); text-transform: uppercase;
  }
  .kicker {
    position: absolute; left: 33px; top: 108px;
    font-family: "Montserrat", sans-serif; font-weight: 700; font-size: 11px; color: var(--gold);
  }
  .body-copy {
    position: absolute; left: 33px; top: 127px; width: 150px;
    font-family: "Montserrat", sans-serif; font-size: 5.6px; line-height: 1.35; color: var(--muted); text-align: justify;
  }
  .body-copy strong { color: var(--paper); }

  .folio {
    position: absolute; bottom: 18px; left: 33px; display: flex; gap: 34px;
    font-family: "Montserrat", sans-serif; font-size: 4.8px; font-weight: 700; color: var(--ink-deep);
  }

  /* Cover */
  .cover-title {
    position: absolute; left: 45px; top: 70px;
    font-weight: 400; font-size: 24px; line-height: 1.05; color: var(--paper);
  }
  .cover-title .accent { color: var(--gold); }
  .cover-rule { position: absolute; left: 45px; top: 128px; width: 128px; height: 1px; background: var(--gold); }
  .cover-sub {
    position: absolute; left: 45px; top: 137px;
    font-size: 11px; line-height: 1.15; color: var(--paper); font-weight: 400;
  }
  .cover-brand {
    position: absolute; left: 205px; top: 282px; display: flex; align-items: center; gap: 6px;
    font-size: 9px; color: var(--ink); font-weight: 400; letter-spacing: .3px;
  }
  .cover-brand::before { content: ""; width: 14px; height: 14px; border: 2px solid var(--gold); }

  /* Contents */
  .toc { position: absolute; left: 33px; top: 107px; width: 245px; list-style: none; }
  .toc li { position: relative; padding-left: 18px; height: 20.5px; font-family: "Montserrat", sans-serif; }
  .toc li::before {
    content: ""; position: absolute; left: 2px; top: 2px; width: 4px; height: 4px;
    background: var(--gold); transform: rotate(45deg);
  }
  .toc .entry { display: flex; font-size: 5.4px; font-weight: 700; color: var(--paper); }
  .toc .entry .dots { flex: 1; border-bottom: 1px dotted var(--muted); margin: 0 2px 1.5px; }
  .toc .note { font-size: 5.2px; color: var(--muted); }
</style>
</head>
<body>

<!-- Cover -->
<section class="page col-1 row-1">
  <svg class="page-art" viewBox="0 0 375 533" preserveAspectRatio="none" aria-hidden="true">
    <polygon points="264,173 375,284 375,533 0,533 0,368 69,368" fill="var(--gold)"/>
    <polygon points="0,346 91,346 69,368 0,368" fill="var(--paper)"/>
    <polygon points="264,198 424,358 264,518 104,358" fill="var(--paper)"/>
    <polygon points="375,470 375,533 312,533" fill="var(--mist)"/>
    <polyline points="375,60 275,140 375,220" fill="none" stroke="var(--gold)" stroke-width=".7"/>
    <polyline points="0,200 110,290 0,380" fill="none" stroke="var(--gold)" stroke-width=".7"/>
    <polyline points="0,420 90,483 0,533" fill="none" stroke="var(--paper)" stroke-width=".5" opacity=".5"/>
  </svg>
  <h1 class="cover-title">DISTRIBUTOR<br><span class="accent">PROGRAM GUIDE</span></h1>
  <div class="cover-rule"></div>
  <p class="cover-sub">DIESEL GENERATORS,<br>ALTERNATORS &amp; PARTS</p>
  <div class="cover-brand">BRIGHTLINE ENERGY</div>
  <div class="photo" role="img" aria-label="Diesel generator set product photo" style="left:143px;top:326px;width:224px;height:88px;"></div>
</section>

<!-- Rental generators -->
<section class="page col-2 row-1">
  <svg class="page-art" viewBox="0 0 375 533" preserveAspectRatio="none" aria-hidden="true">
    <polygon points="264,173 375,284 375,533 0,533 0,368 69,368" fill="var(--gold)"/>
    <polygon points="0,346 91,346 69,368 0,368" fill="var(--paper)"/>
    <polygon points="264,198 424,358 264,518 104,358" fill="var(--paper)"/>
    <polygon points="375,470 375,533 312,533" fill="var(--mist)"/>
    <polyline points="375,60 285,140 375,220" fill="none" stroke="var(--gold)" stroke-width=".7"/>
    <polyline points="0,220 90,300 0,380" fill="none" stroke="var(--gold)" stroke-width=".7"/>
  </svg>
  <div class="section-tag"><span>OUR STOCK</span></div>
  <div class="brand">BRIGHTLINE ENERGY</div>
  <h2 class="page-title">RENTAL GENERATORS</h2>
  <h3 class="kicker">CONTROLLERS</h3>
  <p class="body-copy">Our rental fleet covers short and long term needs with reliable diesel units, delivered, installed and serviced by our own technicians. Every controller is tested before dispatch, so power arrives ready for site work, events, construction and emergency backup across the region.</p>
  <div class="photo" role="img" aria-label="Industrial AC alternator product photo" style="left:208px;top:270px;width:156px;height:160px;"></div>
  <div class="folio"><span>8</span><span>WWW.BRIGHTLINEENERGYCO.EXAMPLE</span></div>
</section>

<!-- Contents -->
<section class="page col-3 row-1">
  <svg class="page-art" viewBox="0 0 375 533" preserveAspectRatio="none" aria-hidden="true">
    <polygon points="0,402 150,402 132,420 0,420" fill="var(--paper)"/>
    <polygon points="260,274 440,454 260,634 80,454" fill="var(--paper)"/>
    <polygon points="0,420 132,420 245,533 0,533" fill="var(--gold)"/>
    <polygon points="375,470 375,533 312,533" fill="var(--mist)"/>
    <polyline points="375,140 290,220 375,300" fill="none" stroke="var(--gold)" stroke-width=".7"/>
    <polyline points="0,300 80,375 0,450" fill="none" stroke="var(--gold)" stroke-width=".7"/>
  </svg>
  <div class="section-tag"><span>INDEX</span></div>
  <div class="brand">BRIGHTLINE ENERGY</div>
  <h2 class="page-title">TABLE OF CONTENT</h2>
  <ol class="toc">
    <li><div class="entry">Company overview and history<span class="dots"></span>01</div><div class="note">Who we are and how we serve our clients</div></li>
    <li><div class="entry">Diesel generators for every site<span class="dots"></span>02</div><div class="note">Prime and continuous power from trusted engines</div></li>
    <li><div class="entry">Alternators and voltage regulators<span class="dots"></span>03</div><div class="note">Stable output for industrial and marine use</div></li>
    <li><div class="entry">Transfer switches and panels<span class="dots"></span>04</div><div class="note">Automatic and manual switching made simple</div></li>
    <li><div class="entry">Rental generators and fleet<span class="dots"></span>05</div><div class="note">Short and long term power on demand</div></li>
    <li><div class="entry">Standby generators for homes<span class="dots"></span>06</div><div class="note">Backup power that starts when you need it</div></li>
    <li><div class="entry">Engine and alternator parts catalog<span class="dots"></span>07</div><div class="note">Genuine parts shipped worldwide from stock</div></li>
    <li><div class="entry">Custom fabrication and enclosures<span class="dots"></span>08</div><div class="note">Sound attenuated housings built to order</div></li>
    <li><div class="entry">Service, support and contact<span class="dots"></span>09</div><div class="note">Our team is ready to help</div></li>
  </ol>
  <div class="photo" role="img" aria-label="Diesel generator set product photo" style="left:204px;top:380px;width:160px;height:58px;"></div>
  <div class="folio"><span>2</span><span>WWW.BRIGHTLINEENERGYCO.EXAMPLE</span></div>
</section>

<!-- About -->
<section class="page col-1 row-2">
  <svg class="page-art" viewBox="0 0 375 533" preserveAspectRatio="none" aria-hidden="true">
    <polygon points="0,338 108,338 90,357 0,357" fill="var(--paper)"/>
    <polygon points="239,162 430,353 239,544 48,353" fill="var(--paper)"/>
    <polygon points="0,357 84,357 250,533 0,533" fill="var(--gold)"/>
    <polygon points="375,470 375,533 312,533" fill="var(--mist)"/>
    <polyline points="375,85 280,160 375,235" fill="none" stroke="var(--gold)" stroke-width=".7"/>
    <polyline points="0,200 80,270 0,340" fill="none" stroke="var(--gold)" stroke-width=".7"/>
  </svg>
  <div class="section-tag"><span>ABOUT US</span></div>
  <div class="brand">BRIGHTLINE ENERGY</div>
  <h2 class="page-title" style="top:70px;">ABOUT OUR<br>COMPANY</h2>
  <p class="body-copy" style="top:133px;width:150px;"><strong>BRIGHTLINE ENERGY LIMITED, INC</strong> is a Larkspur Bay based company specializing in the worldwide sale of Diesel Generators, Transfer Switches, Custom Fabrication, AC Alternators, Automatic Voltage Regulators, Engine and Alternator Parts, as well as a very comprehensive line of products and accessories for the power generation industry.</p>
  <div class="photo" role="img" aria-label="Diesel generator set product photo" style="left:119px;top:310px;width:240px;height:72px;"></div>
  <div class="folio"><span>3</span><span>WWW.BRIGHTLINEENERGYCO.EXAMPLE</span></div>
</section>

<!-- Products -->
<section class="page col-2 row-2">
  <svg class="page-art" viewBox="0 0 375 533" preserveAspectRatio="none" aria-hidden="true">
    <polygon points="0,338 108,338 90,357 0,357" fill="var(--paper)"/>
    <polygon points="239,162 430,353 239,544 48,353" fill="var(--paper)"/>
    <polygon points="0,357 84,357 250,533 0,533" fill="var(--gold)"/>
    <polygon points="375,470 375,533 312,533" fill="var(--mist)"/>
    <polyline points="375,50 275,135 375,220" fill="none" stroke="var(--gold)" stroke-width=".7"/>
    <polyline points="0,200 80,275 0,350" fill="none" stroke="var(--gold)" stroke-width=".7"/>
  </svg>
  <div class="section-tag"><span>OUR STOCK</span></div>
  <div class="brand">BRIGHTLINE ENERGY</div>
  <h2 class="page-title">OUR PRODUCTS</h2>
  <h3 class="kicker">CONTROLLERS</h3>
  <p class="body-copy">We stock a full range of generator sets, alternators and parts for every application. Our controllers manage starting, load sharing and protection, giving operators clear readings and dependable control from small standby units to large prime power installations.</p>
  <div class="photo" role="img" aria-label="Diesel generator set product photo" style="left:119px;top:310px;width:240px;height:72px;"></div>
  <div class="folio"><span>5</span><span>WWW.BRIGHTLINEENERGYCO.EXAMPLE</span></div>
</section>

<!-- Standby generators -->
<section class="page col-3 row-2">
  <svg class="page-art" viewBox="0 0 375 533" preserveAspectRatio="none" aria-hidden="true">
    <polygon points="0,338 108,338 90,357 0,357" fill="var(--paper)"/>
    <polygon points="239,162 430,353 239,544 48,353" fill="var(--paper)"/>
    <polygon points="0,357 84,357 250,533 0,533" fill="var(--gold)"/>
    <polygon points="375,470 375,533 312,533" fill="var(--mist)"/>
    <polyline points="375,50 285,135 375,220" fill="none" stroke="var(--gold)" stroke-width=".7"/>
    <polyline points="0,200 80,275 0,350" fill="none" stroke="var(--gold)" stroke-width=".7"/>
  </svg>
  <div class="section-tag"><span>OUR STOCK</span></div>
  <div class="brand">BRIGHTLINE ENERGY</div>
  <h2 class="page-title" style="top:70px;">STANDBY GENERATORS</h2>
  <h3 class="kicker" style="top:116px;">CONTROLLERS</h3>
  <p class="body-copy" style="top:134px;width:180px;">Standby generators start automatically when utility power fails. Our voltage regulators and controllers keep output stable, protect connected equipment and report status, so homes, clinics and businesses stay running through every outage.</p>
  <div class="photo" role="img" aria-label="Automatic voltage regulator circuit board product photo" style="left:179px;top:270px;width:136px;height:200px;"></div>
  <div class="folio"><span>6</span><span>WWW.BRIGHTLINEENERGYCO.EXAMPLE</span></div>
</section>

</body>
</html>
```